Tolbek cards

I want a simple business card that pops.
Logo on one side.
On side two i want.
"Are you thinking about a new building on your property, or renovating an existing structure? Contact".....
Owners Name: Dale Whitacre
Owners Phone number: 610-555-0187
Address:4076 Copper Ridge RD, Millbrook, PA 16920
Committed to Quality, Service, and Integrity

```html
<!DOCTYPE html>
<html lang="en">
<head>
<meta charset="utf-8">
<title>Tolbek Builders – Business Card</title>
<link rel="stylesheet" href="https://fonts.googleapis.com/css2?family=Arimo:ital,wght@0,400;0,700;1,400&display=swap">
<style>
  :root {
    --stage: #5b5b5b;
    --paper: #ffffff;
    --brown-deep: #3f2a1a;
    --brown-text: #4a3322;
    --brown-soft: #5d4332;
    --ink: #1f1a16;
    --grey-text: #555555;
    --rule: #cfcfcf;
    --back-light: #a08c74;
    --back-mid: #7a5e45;
    --back-edge: #4a2f1e;
    --back-copper: #b47c54;
  }
  * { box-sizing: border-box; margin: 0; padding: 0; }
  html, body {
    width: 1200px; height: 1200px; overflow: hidden;
    background: var(--stage);
    font-family: "Arimo", Arial, sans-serif;
  }
  .canvas { position: relative; width: 1200px; height: 1200px; }

  .card { position: absolute; left: 256px; width: 690px; height: 394px; overflow: hidden; }

  /* Front */
  .card-front { top: 158px; background: var(--paper); }
  .intro {
    position: absolute; left: 49px; top: 34px; width: 280px;
    font-style: italic; font-size: 18px; line-height: 24px; color: var(--brown-soft);
    white-space: nowrap;
  }
  .brand {
    position: absolute; right: 48px; top: 58px;
    display: flex; align-items: center; gap: 12px; color: var(--brown-text);
  }
  .brand-square { width: 40px; height: 40px; background: var(--brown-text); }
  .brand-name { font-weight: 700; font-size: 44px; line-height: 1; letter-spacing: 1px; }
  .brand-sub { display: block; font-size: 14px; letter-spacing: 1.5px; margin-top: 4px; }
  .owner {
    position: absolute; left: 49px; top: 254px;
    font-weight: 700; font-size: 26px; letter-spacing: 0.5px; color: var(--brown-deep);
  }
  .rule { position: absolute; left: 49px; width: 592px; top: 289px; height: 1px; background: var(--rule); }
  .phone {
    position: absolute; left: 49px; top: 299px;
    display: flex; align-items: center; gap: 8px; font-size: 15.5px; color: var(--grey-text);
  }
  .phone svg { width: 13px; height: 13px; fill: var(--brown-text); }
  .address { position: absolute; right: 44px; top: 302px; font-size: 15.5px; color: var(--grey-text); }
  .tagline {
    position: absolute; left: 0; right: 0; top: 346px; text-align: center;
    font-size: 16.5px; color: var(--ink);
  }
  .band-line { position: absolute; left: 0; right: 0; top: 370px; height: 3px; background: var(--brown-deep); }
  .band { position: absolute; left: 0; right: 0; top: 377px; height: 17px; background: var(--brown-deep); }

  /* Back */
  .card-back { top: 652px; }
  .back-pattern {
    position: absolute; inset: 0;
    background:
      radial-gradient(ellipse 55% 60% at 48% 45%, var(--back-light) 0%, var(--back-mid) 55%, transparent 100%),
      linear-gradient(90deg, var(--back-edge) 0%, var(--back-mid) 45%, var(--back-copper) 85%, var(--back-edge) 100%);
  }
  .back-brand {
    position: absolute; right: 32px; top: 296px;
    font-weight: 700; font-size: 20px; letter-spacing: 1px; color: #ffffff;
  }
</style>
</head>
<body>
<main class="canvas">
  <section class="card card-front" aria-label="Business card front">
    <p class="intro">Are you thinking about a<br>new building on your<br>property, or renovating an<br>existing structure?</p>
    <div class="brand">
      <span class="brand-square" aria-hidden="true"></span>
      <div class="brand-name">TOLBEK<span class="brand-sub">BUILDERS LLC</span></div>
    </div>
    <h1 class="owner">DALE WHITACRE</h1>
    <div class="rule"></div>
    <p class="phone">
      <svg viewBox="0 0 24 24" aria-hidden="true"><path d="M6.6 10.8a15.1 15.1 0 0 0 6.6 6.6l2.2-2.2a1 1 0 0 1 1-.25 11.4 11.4 0 0 0 3.6.57 1 1 0 0 1 1 1V20a1 1 0 0 1-1 1A17 17 0 0 1 3 4a1 1 0 0 1 1-1h3.5a1 1 0 0 1 1 1c0 1.25.2 2.45.57 3.57a1 1 0 0 1-.25 1z"/></svg>
      610-555-0187
    </p>
    <p class="address">4076 Copper Ridge RD, Millbrook, PA 16920</p>
    <p class="tagline">Committed to Quality, Service, and Integrity</p>
    <div class="band-line"></div>
    <div class="band"></div>
  </section>

  <section class="card card-back" aria-label="Business card back">
    <div class="back-pattern" role="img" aria-label="Repeating embossed brand-mark pattern in bronze and copper tones"></div>
    <span class="back-brand">TOLBEK</span>
  </section>
</main>
</body>
</html>
```